Business card for medical clinic

I need an upmarket, modern medical/health business card for my clinic

Contact Information for Business Card

name, address, email, qr code

```html
<!DOCTYPE html>
<html lang="en">
<head>
<meta charset="utf-8">
<title>Meridian Care Clinic – Business Card</title>
<link rel="stylesheet" href="https://fonts.googleapis.com/css2?family=Montserrat:wght@500;600;700&display=swap">
<style>
  :root {
    --page-bg: #e6e9ec;
    --card-bg: #f8fafb;
    --ink: #1b1f24;
    --brand-dark: #1d5670;
    --brand-teal: #1f7a86;
    --name-blue: #2a9fd6;
    --accent-bar: #1e6f8f;
    --band-start: #1f7a86;
    --band-mid: #1d4d6e;
    --band-end: #14243a;
  }
  * { margin: 0; padding: 0; box-sizing: border-box; }
  html, body {
    width: 1200px; height: 969px; overflow: hidden;
    background: var(--page-bg);
    font-family: "Montserrat", sans-serif;
  }
  .business-card {
    position: absolute; left: 60px; top: 177px;
    width: 1080px; height: 615px;
    background: var(--card-bg);
    border-radius: 28px;
    overflow: hidden;
    box-shadow: 0 10px 30px rgba(20, 36, 58, 0.15);
  }
  .brand {
    position: absolute; left: 44px; top: 92px;
    display: flex; align-items: center; gap: 16px;
  }
  .brand-dot {
    width: 40px; height: 40px; border-radius: 50%;
    background: var(--brand-teal);
  }
  .brand-name {
    font-weight: 600; font-size: 30px; letter-spacing: 2px;
    color: var(--brand-dark);
  }
  .address {
    position: absolute; left: 44px; top: 250px;
    font-weight: 500; font-size: 26px; line-height: 40px;
    color: var(--ink);
  }
  .contact-list {
    position: absolute; left: 44px; top: 372px;
    list-style: none;
  }
  .contact-item {
    display: flex; align-items: center; gap: 17px;
    height: 39px;
    font-weight: 500; font-size: 26px; color: var(--ink);
  }
  .contact-icon { width: 26px; height: 26px; flex: none; }
  .person {
    position: absolute; right: 46px; top: 218px;
    text-align: right;
  }
  .person-name {
    font-weight: 700; font-size: 38px; line-height: 48px;
    color: var(--name-blue);
  }
  .person-title {
    font-weight: 500; font-size: 25px; line-height: 36px;
    color: var(--ink);
  }
  .accent-bar {
    position: absolute; right: 0; top: 231px;
    width: 25px; height: 66px;
    background: var(--accent-bar);
  }
  .footer-band {
    position: absolute; left: 0; bottom: 0;
    width: 1080px; height: 100px;
    background: linear-gradient(90deg, var(--band-start), var(--band-mid) 50%, var(--band-end));
  }
</style>
</head>
<body>
  <div class="business-card">
    <div class="brand">
      <span class="brand-dot"></span>
      <span class="brand-name">MERIDIAN CARE CLINIC</span>
    </div>

    <p class="address">482 Harbor Lane, Ste<br>210, Fairview, TX 75069</p>

    <ul class="contact-list">
      <li class="contact-item">
        <svg class="contact-icon" viewBox="0 0 24 24" aria-hidden="true">
          <path fill="#1e6f8f" d="M2 8c0-3 5-4 10-4s10 1 10 4v2h-5V8c-1-1-9-1-10 0v2H2zM6 11h12l2 9H4z"/>
          <circle cx="12" cy="15" r="2.5" fill="#f8fafb"/>
        </svg>
        <span>555-214-3870</span>
      </li>
      <li class="contact-item">
        <svg class="contact-icon" viewBox="0 0 24 24" aria-hidden="true">
          <rect x="1" y="5" width="22" height="14" fill="#1e6f8f"/>
          <path d="M1 5l11 8 11-8" fill="none" stroke="#f8fafb" stroke-width="1.6"/>
        </svg>
        <span>Hello@Meridiancare.com</span>
      </li>
      <li class="contact-item">
        <svg class="contact-icon" viewBox="0 0 24 24" aria-hidden="true">
          <circle cx="12" cy="12" r="10" fill="none" stroke="#1e6f8f" stroke-width="2.2"/>
          <ellipse cx="12" cy="12" rx="4.5" ry="10" fill="none" stroke="#1e6f8f" stroke-width="1.8"/>
          <path d="M2 12h20" stroke="#1e6f8f" stroke-width="1.8"/>
        </svg>
        <span>www.Meridiancare.com</span>
      </li>
    </ul>

    <div class="person">
      <p class="person-name">DANA WHITFIELD</p>
      <p class="person-title">Managing Director</p>
    </div>
    <span class="accent-bar"></span>

    <div class="footer-band" role="img" aria-label="Decorative teal to navy footer band"></div>
  </div>
</body>
</html>
```